new signage design for budget motel - Brookfern Lodge

renaming the budget motel as Brookfern Lodge, property located on side of a hill. therefore i choose to name is Brookfern Lodge, im looking for clean, modern look in signage design,this property does not have a Logo, plan to us signage design as a logo as well. current pole sign housing is rectangle shape and will be using same housing I'll be attaching picture of the signage for better idea. looking forward to awesome creative designs.

Industry/Entity Type

Motel

Font styles to use
Serif
Sans Serif

Requirements
Should not have
• mountains , mountain(s) with snow , trees, no black color, red color, blue letters, too much green.

```html
<!DOCTYPE html>
<html lang="en">
<head>
<meta charset="UTF-8">
<title>Brookfern Lodge – Pole Sign</title>
<link href="https://fonts.googleapis.com/css2?family=Oswald:wght@500&display=swap" rel="stylesheet">
<style>
  :root {
    --page: #ffffff;
    --sky-deep: #0a8fd9;
    --sky-mid: #4aaee6;
    --sky-light: #d6eaf6;
    --cloud: #eef6fb;
    --ink: #45223f;
    --arrow: #2e1530;
    --frame: #3a1c37;
  }
  html, body {
    margin: 0;
    padding: 0;
    width: 800px;
    height: 1200px;
    overflow: hidden;
    background: var(--page);
  }
  .canvas {
    position: relative;
    width: 800px;
    height: 1200px;
  }
  .sign {
    position: absolute;
    left: 40px;
    top: 420px;
    width: 720px;
    height: 360px;
    box-shadow: 0 2px 6px rgba(0, 0, 0, 0.25);
  }
  .sign svg {
    display: block;
    width: 100%;
    height: 100%;
  }
  .sign-name {
    font-family: "Oswald", "Arial Narrow", sans-serif;
    font-weight: 500;
    fill: var(--ink);
  }
</style>
</head>
<body>
<main class="canvas">
  <section class="sign">
    <svg viewBox="0 0 1390 695" xmlns="http://www.w3.org/2000/svg">
      <defs>
        <linearGradient id="sky-fill" x1="0" y1="0" x2="1" y2="1">
          <stop offset="0" stop-color="var(--sky-deep)"/>
          <stop offset="0.45" stop-color="var(--sky-mid)"/>
          <stop offset="1" stop-color="var(--sky-light)"/>
        </linearGradient>
        <radialGradient id="cloud-haze" cx="0.45" cy="0.75" r="0.6">
          <stop offset="0" stop-color="var(--cloud)" stop-opacity="0.6"/>
          <stop offset="1" stop-color="var(--cloud)" stop-opacity="0"/>
        </radialGradient>
      </defs>

      <g class="sky-backdrop" role="img" aria-label="Photograph of a bright blue sky with soft white clouds">
        <rect width="1390" height="695" fill="url(#sky-fill)"/>
        <rect width="1390" height="695" fill="url(#cloud-haze)"/>
      </g>

      <path class="sign-frame"
            d="M175,49 H1230 A115,96 0 0 0 1345,145 V540 A115,106 0 0 0 1230,646 H175 A125,106 0 0 0 50,540 V145 A125,96 0 0 0 175,49 Z"
            fill="none" stroke="var(--frame)" stroke-width="3"/>

      <path class="up-arrow"
            d="M690,100 L785,195 L738,195 L738,300 L645,300 L645,195 L597,195 Z"
            fill="var(--arrow)"/>

      <text class="sign-name" x="113" y="502" font-size="258"
            textLength="1167" lengthAdjust="spacingAndGlyphs">BROOKFERN LODGE</text>
    </svg>
  </section>
</main>
</body>
</html>
```